Bry7Legal Letterhead

Need a new letterhead for my law firm.
IDENTIFYING INFORMATION BELOW:
Anselmo R Quintara III
Attorney at Law
Address: 2847 Larkspur Blvd, Ste 300, Dallas, TX 75204
Phone: 877-482-6017
Fax: 469-738-1452
Email: bry@bry7legal.example
Website: www.bry7legal.example

Colors
0054AA
0677BA
7BADD7
CADEEF
E8F1F8

Requirements
Must have
• Logo needs to be on the letterhead, along with identifying information which is included in the project description.

```html
<!DOCTYPE html>
<html lang="en">
<head>
<meta charset="utf-8">
<title>Bry7Legal Letterhead</title>
<link href="https://fonts.googleapis.com/css2?family=Arimo:wght@400;700&display=swap" rel="stylesheet">
<style>
  :root {
    --backdrop: #d9dee2;
    --paper: #ffffff;
    --ink: #111111;
    --brand-blue: #0054aa;
    --brand-blue-light: #0677ba;
    --band-dark: #000000;
  }
  * { box-sizing: border-box; margin: 0; padding: 0; }
  html, body {
    width: 1200px;
    height: 960px;
    overflow: hidden;
    background: var(--backdrop);
    font-family: "Arimo", Arial, sans-serif;
    color: var(--ink);
  }
  .letterhead {
    position: absolute;
    left: 270px;
    top: 12px;
    width: 660px;
    height: 935px;
    background: var(--paper);
    box-shadow: 0 2px 10px rgba(0,0,0,0.15);
    overflow: hidden;
  }
  .brand-name {
    position: absolute;
    left: 46px;
    top: 42px;
    font-weight: 700;
    font-size: 28px;
    letter-spacing: 1px;
    color: var(--ink);
    line-height: 1;
  }
  .header-rule {
    position: absolute;
    left: 0;
    top: 0;
  }
  .attorney {
    position: absolute;
    right: 48px;
    top: 50px;
    text-align: right;
  }
  .attorney-name {
    font-weight: 700;
    font-size: 15px;
    line-height: 18px;
  }
  .attorney-title {
    font-size: 9.5px;
    color: var(--brand-blue);
    line-height: 11px;
  }
  .address {
    position: absolute;
    right: 46px;
    top: 82px;
    font-size: 10px;
    line-height: 12px;
  }
  .contact-list {
    position: absolute;
    right: 48px;
    top: 100px;
    list-style: none;
    font-size: 9.5px;
    line-height: 13px;
    text-align: right;
  }
  .contact-list li {
    display: flex;
    justify-content: flex-end;
    align-items: center;
    gap: 8px;
  }
  .contact-list svg { width: 9px; height: 9px; fill: var(--brand-blue); }
  .band-blue {
    position: absolute;
    left: 0;
    right: 0;
    top: 886px;
    height: 24px;
    background: linear-gradient(90deg, var(--brand-blue-light), var(--brand-blue) 40%, #003f86);
  }
  .band-dark {
    position: absolute;
    left: 0;
    right: 0;
    top: 910px;
    height: 25px;
    background: var(--band-dark);
  }
</style>
</head>
<body>
  <main class="letterhead">
    <div class="brand-name">Bry7Legal</div>

    <svg class="header-rule" width="660" height="120" viewBox="0 0 660 120" aria-hidden="true">
      <polyline points="46,93 255,93 264,71 542,71" fill="none" stroke="#0677ba" stroke-width="1.2"/>
    </svg>

    <div class="attorney">
      <div class="attorney-name">Anselmo R Quintara III</div>
      <div class="attorney-title">Attorney at Law</div>
    </div>

    <div class="address">2847 Larkspur Blvd, Ste 300, Dallas, TX 75204</div>

    <ul class="contact-list">
      <li>877-482-6017
        <svg viewBox="0 0 10 10" aria-label="Phone"><path d="M2 0.5 L3.6 2.6 L2.8 3.6 Q4 6 6.4 7.2 L7.4 6.4 L9.5 8 L8.4 9.5 Q2.8 9 0.5 1.6 Z"/></svg>
      </li>
      <li>469-738-1452
        <svg viewBox="0 0 10 10" aria-label="Fax"><rect x="2.5" y="0.5" width="5" height="3"/><rect x="0.5" y="3.8" width="9" height="4"/><rect x="2.5" y="6.5" width="5" height="3" fill="#fff" stroke="#0054aa" stroke-width="0.8"/></svg>
      </li>
      <li>bry@bry7legal.example
        <svg viewBox="0 0 10 10" aria-label="Email"><rect x="0.5" y="2" width="9" height="6.5"/><polyline points="0.8,2.3 5,5.8 9.2,2.3" fill="none" stroke="#fff" stroke-width="0.9"/></svg>
      </li>
      <li>www.bry7legal.example
        <svg viewBox="0 0 10 10" aria-label="Website"><circle cx="5" cy="5" r="4.5"/><path d="M0.5 5 H9.5 M5 0.5 V9.5 M5 0.5 Q2 5 5 9.5 M5 0.5 Q8 5 5 9.5" fill="none" stroke="#fff" stroke-width="0.7"/></svg>
      </li>
    </ul>

    <div class="band-blue"></div>
    <div class="band-dark"></div>
  </main>
</body>
</html>
```